Website für Geschenkartikel sucht ein Flyer Design
Zielgruppe
Wir vermitteln Geschenkartikel und Erlebnisgeschenke
Aufgabenstellung
Wir suchen ein Flyerdesign im Format Din Lang. Das Design sollte vielleicht etwas an unsere Website www.blauer-kieselweg.de angepasst sein. Es würde uns gefallen, wenn unser "Hauptbanner" integriert werden würde. Das Format sollte so sein, dass wir den Flyer gleich zum Druck weitergeben können.

```html
<!DOCTYPE html>
<html lang="de">
<head>
<meta charset="utf-8">
<title>Flyer DIN lang – Vorder- und Rückseite</title>
<link rel="stylesheet" href="https://fonts.googleapis.com/css2?family=Archivo+Narrow:wght@700&family=Open+Sans:wght@400&family=Caveat:wght@400;600&display=swap">
<style>
  :root {
    --page: #ffffff;
    --ink: #1a1a1a;
    --brand-red: #b3121f;
    --panel-red: #b0141f;
    --note: #f4f4f2;
    --badge: #2f2f2f;
    --line: #222222;
  }
  * { box-sizing: border-box; margin: 0; padding: 0; }
  html, body { width: 1200px; height: 848px; overflow: hidden; background: var(--page); }
  .canvas { position: relative; width: 1200px; height: 848px; }

  .card { position: absolute; background: var(--page); border: 1.5px solid var(--line); overflow: hidden; }

  /* Front */
  .card--front { left: 52px; top: 52px; width: 754px; height: 376px; }
  .front-visual {
    position: absolute; left: 240px; top: 0; width: 514px; height: 376px;
    background: linear-gradient(90deg, #e8e4e2 0%, #c9b7b1 22%, #e23a63 55%, #c8103b 100%);
  }
  .note {
    position: absolute; left: 26px; top: 16px; width: 244px; height: 285px;
    background: var(--note); transform: rotate(-1.5deg);
    box-shadow: 3px 4px 8px rgba(0,0,0,.25);
    font-family: "Caveat", cursive; color: var(--ink); text-align: center;
  }
  .note__title { font-size: 48px; font-weight: 600; margin-top: 52px; text-decoration: underline; text-underline-offset: 6px; }
  .note__text { font-size: 29px; line-height: 38px; margin-top: 16px; padding: 0 14px; }
  .front-url {
    position: absolute; left: 28px; top: 336px;
    font-family: "Archivo Narrow", sans-serif; font-weight: 700; font-size: 25px; color: var(--brand-red);
  }

  /* Back */
  .card--back { left: 381px; top: 411px; width: 756px; height: 377px; }
  .offer-panel {
    position: absolute; left: 27px; top: 30px; width: 436px; height: 263px;
    background: var(--panel-red); border-radius: 12px;
  }
  .categories {
    position: absolute; left: 21px; top: 10px; width: 396px;
    font-family: "Open Sans", sans-serif; font-size: 18.5px; line-height: 25px; color: #fff;
  }
  .categories li { list-style: none; display: flex; justify-content: space-between; white-space: nowrap; }
  .boxes-visual {
    position: absolute; left: 14px; top: 168px; width: 276px; height: 156px;
    background: linear-gradient(180deg, #e0b27a 0%, #c8945a 100%); border-radius: 4px;
  }
  .try-badge {
    position: absolute; left: 296px; top: 142px; width: 136px; height: 136px; border-radius: 50%;
    background: var(--badge); border: 5px solid #fff;
    display: flex; flex-direction: column; align-items: center; justify-content: center;
    font-family: "Caveat", cursive; color: #fff; font-size: 38px; line-height: 34px;
  }
  .back-url {
    position: absolute; left: 29px; top: 334px;
    font-family: "Archivo Narrow", sans-serif; font-weight: 700; font-size: 16px; color: var(--brand-red);
  }
  .address-rule { position: absolute; left: 486px; top: 144px; width: 2px; height: 179px; background: var(--line); }
  .gift-visual {
    position: absolute; left: 617px; top: 30px; width: 110px; height: 102px;
    background: linear-gradient(180deg, #f3f3f3 0%, #d9d9d9 100%);
  }
</style>
</head>
<body>
<main class="canvas">
  <section class="card card--front" aria-label="Vorderseite">
    <div class="front-visual" role="img" aria-label="Foto einer jungen Frau mit Geschenk vor pinkem Strahlenhintergrund und offenem Geschenkkarton mit Herzen"></div>
    <div class="note">
      <p class="note__title">Hier</p>
      <p class="note__text">finden Sie immer das passende Geschenk.</p>
    </div>
    <p class="front-url">Blauer-kieselweg.de</p>
  </section>

  <section class="card card--back" aria-label="Rückseite">
    <div class="offer-panel">
      <ul class="categories">
        <li><span>Partner</span><span>·</span><span>Freunde</span><span>·</span><span>Lustiges</span><span>·</span><span>Wohnen</span></li>
        <li><span>Personalisiertes</span><span>·</span><span>Textilien</span><span>·</span><span>Elektronik</span></li>
        <li><span>Nach Preis</span><span>·</span><span>Erlebnisgeschenke</span><span>·</span><span>Poster</span></li>
      </ul>
      <div class="try-badge"><span>Jetzt</span><span>testen</span></div>
    </div>
    <div class="boxes-visual" role="img" aria-label="Gestapelte Versandkartons"></div>
    <p class="back-url">Blauer-kieselweg.de</p>
    <div class="address-rule"></div>
    <div class="gift-visual" role="img" aria-label="Weißes Geschenkpaket mit roter Schleife"></div>
  </section>
</main>
</body>
</html>
```